Brell Stone Company Business Cards

Front and Back Business Card - logo and text setup - cool design. I need workable photoshop or illustrator files so I can setup each employee card with design that is created
Updates

Hi everyone, thank you for the great entries. Please no more white and blue cards - there are so many already - black and silver only now please. thanks!

Target Market(s)

Construction Industry - Facility Managers

Industry/Entity Type

Construction

Contact Information for Business Card

I really like contemporary simplistic looks - clean neat....not opposed to seeing some black backrounds

Requirements
Must have
• Logo/website address with design on front only - www.brellstone-example.com (logo attached)
• Back:
• Name/Title/Company Address/Phone/email address
Nice to have
• Cool design
Should not have
• Nothing gimmicky like Fire or Water - since we are a Fire Protection company - it has all been done

```html
<!DOCTYPE html>
<html lang="en">
<head>
<meta charset="utf-8">
<title>Brell Stone Company – Business Cards</title>
<link href="https://fonts.googleapis.com/css2?family=Source+Sans+3:wght@400;600;800&display=swap" rel="stylesheet">
<style>
  :root {
    --stage: #2a2a2c;
    --card: #1d1d1f;
    --card-edge: #303033;
    --silver: #b9bcc0;
    --brand-blue: #2f4f8f;
    --brand-red: #ea4a35;
    --text: #f1f1f1;
    --rule: #6a6a6e;
  }
  * { margin: 0; padding: 0; box-sizing: border-box; }
  html, body { width: 1200px; height: 874px; overflow: hidden; }
  body {
    background: var(--stage);
    font-family: "Source Sans 3", Arial, sans-serif;
    position: relative;
  }
  .card {
    position: absolute;
    width: 580px;
    height: 330px;
    background: var(--card);
    border: 1px solid var(--card-edge);
    border-radius: 22px;
    box-shadow: 0 10px 30px rgba(0,0,0,.45);
  }
  .card--front { left: 330px; top: 50px; }
  .card--back  { left: 290px; top: 480px; }

  .front-name {
    position: absolute;
    left: 0; right: 0; top: 118px;
    text-align: center;
    font-weight: 800;
    font-size: 82px;
    letter-spacing: -1px;
    color: var(--silver);
    line-height: 1;
  }

  .back-name {
    position: absolute;
    left: 0; right: 0; top: 40px;
    text-align: center;
    font-weight: 800;
    font-size: 64px;
    letter-spacing: -1px;
    color: var(--brand-blue);
    line-height: 1;
  }

  .person {
    position: absolute;
    right: 310px; top: 170px;
    text-align: right;
    color: var(--text);
    font-size: 17px;
    line-height: 1.3;
  }
  .person__name { color: var(--brand-blue); font-weight: 600; font-size: 24px; }
  .person__title { color: var(--brand-red); font-size: 17px; margin-bottom: 6px; }

  .divider {
    position: absolute;
    left: 290px; top: 180px;
    width: 1px; height: 110px;
    background: var(--rule);
  }

  .contact {
    position: absolute;
    left: 310px; top: 180px;
    list-style: none;
    color: var(--text);
    font-size: 17px;
    line-height: 1;
  }
  .contact li { display: flex; align-items: center; gap: 10px; height: 27px; }
  .contact svg { width: 15px; height: 15px; fill: var(--brand-blue); flex: none; }
</style>
</head>
<body>
  <section class="card card--front" aria-label="Card front">
    <div class="front-name">Brell Stone</div>
  </section>

  <section class="card card--back" aria-label="Card back">
    <div class="back-name">Brell Stone</div>

    <div class="person">
      <div class="person__name">Dana Whitlow</div>
      <div class="person__title">CEO/Founder</div>
      <div>48 Quarry Lane</div>
      <div>Ridgefield, NY 11900</div>
    </div>

    <div class="divider"></div>

    <ul class="contact">
      <li>
        <svg viewBox="0 0 16 16" aria-hidden="true"><path d="M3 1h3l1.5 4-2 1.3a9 9 0 0 0 4.2 4.2L11 8.5l4 1.5v3a2 2 0 0 1-2 2A12 12 0 0 1 1 3a2 2 0 0 1 2-2z"/></svg>
        (555) 014-2201
      </li>
      <li>
        <svg viewBox="0 0 16 16" aria-hidden="true"><path d="M4 1h8v4H4zM1 6h14v6h-3v3H4v-3H1zm4 4v4h6v-4z"/></svg>
        (555) 014-2202
      </li>
      <li>
        <svg viewBox="0 0 16 16" aria-hidden="true"><path d="M1 3h14v10H1zm1.5 1.2L8 8.5l5.5-4.3z"/></svg>
        info@brellstone-example.com
      </li>
      <li>
        <svg viewBox="0 0 16 16" aria-hidden="true"><circle cx="8" cy="8" r="7"/></svg>
        www.brellstone-example.com
      </li>
    </ul>
  </section>
</body>
</html>
```